Copperleaf Roofing Business Card

This is my current business card. But I’d like to make some changes. Somewhere on the card I’d like to list some of the services we offer. Maybe on the back? But I’d still like to keep the red. White and black modern look.

-residential & commercial roofing
-Roof Repairs & Maintenance
-Storm Damage & Insurance Claims specialist
-Christmas Lights and permanent Christmas lights
Fencing. Windows. Gutters. Siding. Sheetrock, painting.

```html
<!DOCTYPE html>
<html lang="en">
<head>
<meta charset="utf-8">
<title>Copperleaf Roofing Business Card</title>
<link rel="stylesheet" href="https://fonts.googleapis.com/css2?family=Michroma&family=Didact+Gothic&family=Roboto+Condensed:wght@400;500&display=swap">
<style>
  :root {
    --red: #e30613;
    --black: #111111;
    --ink: #1a1a1a;
    --white: #ffffff;
    --grey: #8a8a8a;
    --stage: #2b2b2b;
    --back-dark: #161616;
    --back-mid: #3a3a3a;
  }
  * { margin: 0; padding: 0; box-sizing: border-box; }
  html, body { width: 1200px; height: 1108px; overflow: hidden; }
  body {
    background: var(--stage);
    display: flex;
    align-items: center;
    justify-content: center;
    gap: 70px;
  }
  .card {
    width: 440px;
    height: 770px;
    border-radius: 26px;
    position: relative;
    overflow: hidden;
  }
  /* Front */
  .card-front {
    background: var(--white);
    display: flex;
    flex-direction: column;
    align-items: center;
    padding-top: 70px;
    font-family: "Didact Gothic", sans-serif;
    color: var(--ink);
  }
  .brand-mark {
    width: 170px;
    height: 170px;
    border-radius: 50%;
    background: var(--red);
  }
  .brand-name {
    margin-top: 34px;
    font-family: "Michroma", sans-serif;
    color: var(--red);
    font-size: 30px;
    line-height: 1.25;
    text-align: center;
    letter-spacing: 1px;
  }
  .person-name {
    margin-top: 64px;
    font-family: "Michroma", sans-serif;
    font-size: 30px;
    letter-spacing: 1px;
  }
  .person-name .first { color: var(--red); }
  .person-name .last { color: var(--black); }
  .person-role {
    font-size: 26px;
    letter-spacing: 1px;
    margin-top: 4px;
  }
  .contact-rule {
    margin-top: 18px;
    width: 340px;
    display: flex;
    align-items: center;
    gap: 10px;
  }
  .contact-rule::before, .contact-rule::after {
    content: "";
    flex: 1;
    height: 1px;
    background: var(--grey);
  }
  .contact-icon {
    width: 44px;
    height: 44px;
    border-radius: 6px;
    background: var(--red);
    display: flex;
    align-items: center;
    justify-content: center;
  }
  .contact-list {
    margin-top: 20px;
    text-align: center;
    font-size: 25px;
    line-height: 1.45;
    list-style: none;
  }
  .contact-list .accent { color: var(--red); font-weight: 700; }
  /* Back */
  .card-back {
    background: var(--back-dark);
    color: var(--white);
    font-family: "Roboto Condensed", sans-serif;
  }
  .back-pattern {
    position: absolute;
    inset: 0;
    background: linear-gradient(160deg, var(--back-mid) 0%, #242424 40%, var(--back-dark) 75%);
  }
  .back-mark {
    position: absolute;
    left: 200px;
    top: 230px;
    width: 44px;
    height: 44px;
    border-radius: 50%;
    background: var(--red);
  }
  .service-list {
    position: absolute;
    left: 0;
    right: 0;
    top: 420px;
    list-style: none;
    text-align: center;
    font-size: 24px;
    font-weight: 500;
    line-height: 1.3;
  }
  .service-list li + li { margin-top: 4px; }
  .trade-list {
    position: absolute;
    left: 0;
    right: 0;
    top: 640px;
    text-align: center;
    color: var(--red);
    font-size: 21px;
    text-transform: uppercase;
    line-height: 1.5;
  }
</style>
</head>
<body>
  <section class="card card-front">
    <div class="brand-mark"></div>
    <h1 class="brand-name">COPPERLEAF<br>ROOFING CO.</h1>
    <p class="person-name"><span class="first">DANA</span> <span class="last">WHITLOW</span></p>
    <p class="person-role">OWNER</p>
    <div class="contact-rule">
      <span class="contact-icon">
        <svg width="26" height="26" viewBox="0 0 24 24" fill="none" stroke="#fff" stroke-width="2" stroke-linejoin="round"><path d="M5 3h4l2 5-2.5 1.5a11 11 0 0 0 6 6L16 13l5 2v4a2 2 0 0 1-2 2A17 17 0 0 1 3 5a2 2 0 0 1 2-2z"/></svg>
      </span>
      <span class="contact-icon">
        <svg width="26" height="26" viewBox="0 0 24 24" fill="none" stroke="#fff" stroke-width="2"><rect x="3" y="5" width="18" height="14" rx="1"/><path d="M3 6l9 7 9-7"/></svg>
      </span>
      <span class="contact-icon">
        <svg width="26" height="26" viewBox="0 0 24 24" fill="none" stroke="#fff" stroke-width="2"><circle cx="12" cy="12" r="9"/><path d="M3 12h18M12 3a14 14 0 0 1 0 18M12 3a14 14 0 0 0 0 18"/></svg>
      </span>
    </div>
    <ul class="contact-list">
      <li>682-555-0148</li>
      <li>dana@copperleafroofing.co</li>
      <li>www.<span class="accent">copperleafroofing</span>.co</li>
    </ul>
  </section>

  <section class="card card-back">
    <div class="back-pattern" role="img" aria-label="Tonal repeating brand emblem pattern fading from grey to black"></div>
    <div class="back-mark"></div>
    <ul class="service-list">
      <li>Residential &amp; Commercial Roofing</li>
      <li>Roof Repairs &amp; Maintenance</li>
      <li>Storm Damage &amp; Insurance<br>Claims Specialist</li>
      <li>Christmas Lights and Permanent<br>Christmas Lights</li>
    </ul>
    <p class="trade-list">Fencing • Windows • Gutters • Siding<br>Sheetrock • Painting</p>
  </section>
</body>
</html>
```